Harrow Grading LLC business card design

Excavation company business cards

Contact Information for Business Card

Harrow Grading LLC cell phone 208-417-6290 office phone 208-319-4856 harrowgradingllc@maplecove.com Driveways, site prep, retaining walls, septic systems, rock delivery

Colors

Designer to choose colors to be used in the design.

```html
<!DOCTYPE html>
<html lang="en">
<head>
<meta charset="utf-8">
<title>Harrow Grading LLC – Business Card</title>
<link href="https://fonts.googleapis.com/css2?family=Arimo:wght@400;700&family=Michroma&display=swap" rel="stylesheet">
<style>
  :root {
    --backdrop: #363636;
    --orange: #e96c1f;
    --white: #ffffff;
    --slate: #5f6062;
    --band-grey: #646464;
    --ink-grey: #555658;
  }
  * { box-sizing: border-box; margin: 0; padding: 0; }
  html, body {
    width: 1075px; height: 1200px; overflow: hidden;
    background: var(--backdrop);
    font-family: "Arimo", Arial, sans-serif;
  }
  .card {
    position: absolute; left: 206px; width: 663px; height: 396px;
    box-shadow: 3px 3px 2px rgba(0,0,0,0.6);
    overflow: hidden;
  }
  .card--front { top: 187px; background: var(--white); }
  .card--back { top: 637px; background: var(--orange); }

  .brand-name {
    position: absolute; left: 0; right: 0; text-align: center;
    font-family: "Michroma", "Arimo", sans-serif;
    letter-spacing: 1px; line-height: 1.25;
  }
  .card--front .brand-name {
    left: 330px; right: 34px; top: 96px;
    font-size: 24px; color: var(--orange);
  }
  .card--back .brand-name {
    top: 150px; font-size: 36px; color: var(--white);
  }

  .holder { position: absolute; left: 38px; top: 218px; }
  .holder__name {
    font-family: "Michroma", "Arimo", sans-serif;
    font-size: 19px; color: var(--orange); letter-spacing: 0.5px;
  }
  .holder__role { font-size: 18px; color: var(--ink-grey); margin-top: 2px; }
  .holder__rule {
    position: absolute; left: 36px; top: 274px;
    width: 255px; height: 5px; background: var(--slate);
  }

  .contact-band {
    position: absolute; left: 0; top: 277px; width: 100%; height: 119px;
    background: var(--orange); color: var(--white); font-size: 19px;
  }
  .contact-list { position: absolute; left: 37px; top: 20px; list-style: none; }
  .contact-list li { display: flex; align-items: center; height: 23.5px; }
  .contact-list svg { width: 18px; height: 18px; margin-right: 7px; fill: var(--white); }
  .address {
    position: absolute; right: 49px; top: 20px;
    text-align: right; line-height: 23.5px; font-style: normal;
  }

  .services-band {
    position: absolute; left: 0; top: 340px; width: 100%; height: 37px;
    background: var(--band-grey); color: var(--white);
    font-size: 19px; display: flex; align-items: center; justify-content: center;
  }
</style>
</head>
<body>
  <section class="card card--front">
    <div class="brand-name">HARROW GRADING LLC</div>
    <div class="holder">
      <div class="holder__name">DANIEL REYES</div>
      <div class="holder__role">Managing Director</div>
    </div>
    <div class="holder__rule"></div>
    <div class="contact-band">
      <ul class="contact-list">
        <li><svg viewBox="0 0 24 24"><path d="M7 1h10a2 2 0 0 1 2 2v18a2 2 0 0 1-2 2H7a2 2 0 0 1-2-2V3a2 2 0 0 1 2-2zm0 3v14h10V4zm5 15.5a1.2 1.2 0 1 0 0 2.4 1.2 1.2 0 0 0 0-2.4z"/></svg>208-417-6290</li>
        <li><svg viewBox="0 0 24 24"><path d="M6.6 10.8a15.1 15.1 0 0 0 6.6 6.6l2.2-2.2a1 1 0 0 1 1-.25 11.4 11.4 0 0 0 3.6.57 1 1 0 0 1 1 1V20a1 1 0 0 1-1 1A17 17 0 0 1 3 4a1 1 0 0 1 1-1h3.5a1 1 0 0 1 1 1c0 1.25.2 2.45.57 3.57a1 1 0 0 1-.25 1z"/></svg>208-319-4856</li>
        <li><svg viewBox="0 0 24 24"><path d="M2 5h20v14H2zm2 2v.5l8 5.5 8-5.5V7zm0 3v7h16v-7l-8 5.5z"/></svg>harrowgradingllc@maplecove.com</li>
      </ul>
      <address class="address">421, Address line<br>goes here, 45452<br>Country Name</address>
    </div>
  </section>

  <section class="card card--back">
    <div class="brand-name">HARROW<br>GRADING LLC</div>
    <div class="services-band">Driveways | Site prep | Retaining walls | Septic systems | Rock delivery</div>
  </section>
</body>
</html>
```